Coffeeshop menu for filter tip

We want to have a cannabis (coffeeshop) menu in the size 25mm wide x 60mm wide. Some examples attached.

it must have the following text:
Menu

WEED p/g
Oblivane €16
Cloudplum €14
Tide Runner €14
Quincefig €16
Mega Marsh €14
Grey Heron €14

HASH p/g
Tashar Amber €12
Pebble Frost€11
Lime Dunes €14
Ash Petal €10

Target Market(s)

tourist in Amsterdam

Requirements
Nice to have
• cannabis sign leaf
• No Cigarettes allowed symbol

```html
<!DOCTYPE html>
<html lang="en">
<head>
<meta charset="utf-8">
<title>Coffeeshop Menu</title>
<link href="https://fonts.googleapis.com/css2?family=Montserrat:wght@700&family=Michroma&family=Saira+Semi+Condensed:wght@500;600&display=swap" rel="stylesheet">
<style>
  :root{
    --bg-outer:#111c14;
    --panel-top:#13201a;
    --panel-bottom:#1f6a24;
    --box-fill:#0b130e;
    --green:#2ccf2c;
    --green-line:#22b422;
    --tab-text:#0a0f0b;
    --title-grey:#c9c9c9;
    --label-grey:#a9a9a9;
    --price-white:#ffffff;
    --badge-red:#e4231f;
    --badge-ink:#0a0a0a;
  }
  *{box-sizing:border-box;margin:0;padding:0}
  html,body{width:1200px;height:2880px;overflow:hidden;background:var(--bg-outer)}
  .menu-card{position:relative;width:1200px;height:2880px;background:var(--bg-outer)}
  .panel{position:absolute;left:67px;top:67px;width:1066px;height:2746px;
    background:linear-gradient(180deg,var(--panel-top) 0%,#15271b 45%,#1a4a20 75%,var(--panel-bottom) 100%)}
  .leaf-art{position:absolute;border-radius:50%}
  .leaf-art--top{left:620px;top:0;width:446px;height:760px;
    background:radial-gradient(ellipse at 70% 40%,rgba(44,207,44,.22),rgba(44,207,44,0) 70%)}
  .leaf-art--left{left:0;top:500px;width:300px;height:760px;
    background:radial-gradient(ellipse at 30% 50%,rgba(44,207,44,.14),rgba(44,207,44,0) 70%)}
  .leaf-art--bottom{left:0;top:1900px;width:640px;height:846px;
    background:radial-gradient(ellipse at 35% 60%,rgba(60,220,60,.35),rgba(60,220,60,0) 70%)}
  .title{position:absolute;left:122px;top:150px;font-family:"Montserrat",sans-serif;font-weight:700;
    font-size:176px;line-height:176px;letter-spacing:12px;color:var(--title-grey)}
  .section{position:absolute;left:163px;width:877px;border:3px solid var(--green-line);
    background:rgba(11,19,14,.82)}
  .section--weed{top:499px;height:1042px}
  .section--hash{top:1709px;height:752px}
  .section-tab{position:absolute;left:-3px;top:-3px;width:314px;height:89px;background:var(--green);
    font-family:"Michroma",sans-serif;font-size:56px;line-height:89px;color:var(--tab-text);
    padding-left:34px;letter-spacing:1px}
  .unit{position:absolute;right:56px;top:40px;font-family:"Saira Semi Condensed",sans-serif;
    font-weight:500;font-size:54px;color:var(--label-grey)}
  .items{position:absolute;left:58px;right:56px;top:146px;list-style:none}
  .item{display:flex;align-items:baseline;height:144px;line-height:144px}
  .item-name{font-family:"Saira Semi Condensed",sans-serif;font-weight:500;font-size:66px;
    color:var(--green);text-transform:uppercase;white-space:nowrap}
  .leader{flex:1;margin-left:18px;border-bottom:2px solid var(--green-line);height:0;align-self:baseline;
    transform:translateY(-4px)}
  .price{width:136px;text-align:right;font-family:"Saira Semi Condensed",sans-serif;font-weight:600;
    font-size:72px;color:var(--price-white)}
  .no-cig{position:absolute;left:838px;top:2539px;width:240px;height:184px;border:4px solid var(--badge-red);
    border-radius:10px;background:rgba(20,60,24,.6)}
  .no-cig svg{position:absolute;left:14px;top:12px}
  .no-cig-label{position:absolute;left:0;right:0;bottom:14px;text-align:center;
    font-family:"Saira Semi Condensed",sans-serif;font-weight:600;font-size:31px;color:var(--badge-ink);letter-spacing:1px}
</style>
</head>
<body>
<main class="menu-card">
  <div class="panel">
    <div class="leaf-art leaf-art--top" role="img" aria-label="Green cannabis leaf illustration"></div>
    <div class="leaf-art leaf-art--left" role="img" aria-label="Faint cannabis leaf illustration"></div>
    <div class="leaf-art leaf-art--bottom" role="img" aria-label="Bright green cannabis leaf illustration"></div>
  </div>

  <h1 class="title">MENU</h1>

  <section class="section section--weed">
    <h2 class="section-tab">WEED</h2>
    <span class="unit">P/G</span>
    <ul class="items">
      <li class="item"><span class="item-name">Oblivane</span><span class="leader"></span><span class="price">€16</span></li>
      <li class="item"><span class="item-name">Cloudplum</span><span class="leader"></span><span class="price">€14</span></li>
      <li class="item"><span class="item-name">Tide Runner</span><span class="leader"></span><span class="price">€14</span></li>
      <li class="item"><span class="item-name">Quincefig</span><span class="leader"></span><span class="price">€16</span></li>
      <li class="item"><span class="item-name">Mega Marsh</span><span class="leader"></span><span class="price">€14</span></li>
      <li class="item"><span class="item-name">Grey Heron</span><span class="leader"></span><span class="price">€14</span></li>
    </ul>
  </section>

  <section class="section section--hash">
    <h2 class="section-tab">HASH</h2>
    <span class="unit">P/G</span>
    <ul class="items">
      <li class="item"><span class="item-name">Tashar Amber</span><span class="leader"></span><span class="price">€12</span></li>
      <li class="item"><span class="item-name">Pebble Frost</span><span class="leader"></span><span class="price">€11</span></li>
      <li class="item"><span class="item-name">Lime Dunes</span><span class="leader"></span><span class="price">€14</span></li>
      <li class="item"><span class="item-name">Ash Petal</span><span class="leader"></span><span class="price">€10</span></li>
    </ul>
  </section>

  <div class="no-cig">
    <svg width="204" height="112" viewBox="0 0 204 112" aria-hidden="true">
      <text x="2" y="104" font-family="Montserrat, sans-serif" font-weight="700" font-size="128" fill="#0a0a0a">N</text>
      <circle cx="152" cy="58" r="42" fill="#0a0a0a" stroke="#e4231f" stroke-width="10"/>
      <rect x="122" y="56" width="52" height="12" fill="#e4231f"/>
      <rect x="176" y="56" width="8" height="12" fill="#e4231f"/>
      <line x1="124" y1="30" x2="180" y2="86" stroke="#e4231f" stroke-width="10"/>
    </svg>
    <span class="no-cig-label">CIGARETTES</span>
  </div>
</main>
</body>
</html>
```